Etiketten-Design für Duftsprays
Zielgruppe
Liebe Kreative
Es geht um ein Premium-Etikettendesign für einen Duftspray. Das Bild der Flasche werde ich Anhängen. Das sichtbare Etikett wird 7.2 x 10.8 cm gross sein. Das Etikett wird jedoch aufklappbar sein, d.h ein Teil wird auf den ersten Blick nicht sichtbar sein.
Die Mindestschriftgrösse ist Arial 7.
Das Design soll schlicht und Premium wirken. Wendrasil als Name sollte von oben nach unten geschrieben werden. Dieser Name sollte man hauptsächlich sehen, wenn man es von vorne betrachtet. Wichtig ist noch, dass beim sichtbaren Teil steht „Innenseite beachten“
Sichtbarer Teil:
Wendrasil (Produktname)
Inhalt: 30 ml
Gefahrenpiktogramme (Im Anhang. Auf Etikette 1x1cm gross)
Moravel GMBH
CH-8517 Ruswilen
Tel. 034 582 67 19
Enthält / Contient: 2-Propanol
Wendrasil zweimal auf Kopfhöhe und 30cm vor dem Gesicht in die Luft sprühen und einatmen. Fördert die Konzentration und macht wach.
Innenseite beachten.
Nicht sichtbarer Teil:
ACHTUNG Kann Schläfrigkeit und Benommenheit verursachen Enthält D-Limonen, Citral. Kann allergische Reaktionen hervorrufen. Darf nicht in die Hände von Kindern gelangen.
ATTENTION Peut provoquer somnolence ou vertiges. Contient d-limonène, citral. Peut produire une réaction allergique. Tenir hors de portée des enfants.
Haltbarkeit: Nach dem Öffnen 6 Monate haltbar
Aufgabenstellung
Es ist wichtig, dass das ganze Stilvoll aussieht, es soll eine 'Premium-Ausstrahlung' haben.

```html
<!DOCTYPE html>
<html lang="de">
<head>
<meta charset="utf-8">
<title>Wendrasil – Etikett</title>
<link rel="stylesheet" href="https://fonts.googleapis.com/css2?family=Montserrat:wght@300;400;500&display=swap">
<style>
  :root {
    --bg: #cfcdc8;
    --paper: #ffffff;
    --ink: #4a4a4a;
    --ink-soft: #707070;
    --ink-light: #8a8a8a;
    --blue-light: #cfeaf5;
    --blue-mid: #8fd0ea;
    --blue-deep: #4fb5df;
    --hazard: #e0262b;
    --rule: #6a6a6a;
  }
  * { box-sizing: border-box; margin: 0; padding: 0; }
  html, body { width: 1200px; height: 888px; overflow: hidden; }
  body {
    background: var(--bg);
    font-family: "Montserrat", sans-serif;
    color: var(--ink);
    position: relative;
  }
  .label {
    position: absolute;
    top: 207px;
    height: 474px;
    background: var(--paper);
    box-shadow: 0 6px 14px rgba(0,0,0,0.18);
    overflow: hidden;
  }
  .label--front { left: 87px; width: 317px; }
  .label--inside { left: 479px; width: 633px; }

  .pattern-band {
    position: absolute;
    left: 0; right: 0;
  }
  .pattern-band--top {
    top: 0; height: 46px;
    background: linear-gradient(90deg, var(--blue-light), var(--blue-mid) 50%, var(--blue-light));
    opacity: 0.75;
  }
  .pattern-band--bottom {
    bottom: 0; height: 118px;
    background: linear-gradient(180deg, var(--blue-light), var(--blue-mid) 60%, var(--blue-deep));
    opacity: 0.75;
  }

  .brand-name {
    position: absolute;
    left: 22px; top: 20px;
    height: 432px;
    writing-mode: vertical-rl;
    transform: rotate(180deg);
    font-size: 44px;
    font-weight: 400;
    letter-spacing: 17px;
    line-height: 44px;
    color: var(--ink);
    z-index: 2;
  }

  .front-copy {
    position: absolute;
    left: 97px; width: 185px;
    top: 66px;
    text-align: center;
  }
  .notice { font-size: 12.5px; font-weight: 300; color: var(--ink-soft); }
  .usage {
    margin-top: 20px;
    font-size: 13.6px; font-weight: 300; line-height: 19px;
    text-align: justify; text-align-last: justify;
  }
  .claim { margin-top: 9px; font-size: 13.6px; font-weight: 500; line-height: 19px; }
  .volume { margin-top: 20px; font-size: 17px; font-weight: 400; letter-spacing: 2px; }
  .maker { margin-top: 18px; font-size: 10.5px; font-weight: 300; line-height: 13px; color: var(--ink-soft); }
  .contents { margin-top: 10px; font-size: 10.5px; font-weight: 300; color: var(--ink-soft); }

  .hazards {
    position: absolute;
    right: 4px; bottom: 2px;
    display: flex; gap: 3px;
    z-index: 2;
  }

  .inside-col {
    position: absolute;
    font-size: 12px; font-weight: 300; line-height: 18.6px;
    color: var(--ink-soft);
    text-align: justify;
  }
  .inside-col--info { left: 83px; width: 217px; top: 125px; }
  .inside-col--warnings { left: 337px; width: 268px; top: 107px; }
  .inside-col p + p { margin-top: 18px; }
  .inside-col strong { font-weight: 500; color: var(--ink); }
  .divider {
    position: absolute;
    left: 317px; top: 92px;
    width: 1px; height: 218px;
    background: var(--rule);
  }
</style>
</head>
<body>

  <section class="label label--front" aria-label="Sichtbarer Teil des Etiketts">
    <div class="pattern-band pattern-band--top" role="img" aria-label="Hellblaues Winkelmuster"></div>
    <div class="pattern-band pattern-band--bottom" role="img" aria-label="Hellblaues Winkelmuster"></div>
    <h1 class="brand-name">WENDRASIL</h1>

    <div class="front-copy">
      <p class="notice">Innenseite beachten</p>
      <p class="usage">Wendrasil zweimal auf Kopfhöhe und 30cm vor dem Gesicht in die Luft sprühen und einatmen.</p>
      <p class="claim">Fördert die Konzentration und macht wach.</p>
      <p class="volume">30 ml</p>
      <p class="maker">Moravel GMBH<br>CH-8517 Ruswilen<br>Tel. 034 582 67 19</p>
      <p class="contents">Enthält / Contient: 2-Propanol</p>
    </div>

    <div class="hazards">
      <svg class="hazard-icon" width="44" height="44" viewBox="0 0 44 44" aria-label="Gefahrenpiktogramm Ausrufezeichen" role="img">
        <rect x="8" y="8" width="28" height="28" transform="rotate(45 22 22)" fill="#fff" stroke="var(--hazard)" stroke-width="2.5"/>
        <rect x="20.3" y="12" width="3.4" height="14" rx="1" fill="#111"/>
        <circle cx="22" cy="30.5" r="2.2" fill="#111"/>
      </svg>
      <svg class="hazard-icon" width="44" height="44" viewBox="0 0 44 44" aria-label="Gefahrenpiktogramm Flamme" role="img">
        <rect x="8" y="8" width="28" height="28" transform="rotate(45 22 22)" fill="#fff" stroke="var(--hazard)" stroke-width="2.5"/>
        <path d="M22 12c1 4 6 6 6 12a6 6 0 0 1-12 0c0-3 2-4 2-7 2 2 2 4 3 4 0-3-1-6 1-9z" fill="#111"/>
        <rect x="15" y="31" width="14" height="2" fill="#111"/>
      </svg>
    </div>
  </section>

  <section class="label label--inside" aria-label="Innenseite des Etiketts">
    <div class="pattern-band pattern-band--top" role="img" aria-label="Hellblaues Winkelmuster"></div>
    <div class="pattern-band pattern-band--bottom" role="img" aria-label="Hellblaues Winkelmuster"></div>
    <p class="brand-name" aria-hidden="true">WENDRASIL</p>

    <div class="inside-col inside-col--info">
      <p>Lorem ipsum dolor sit amet, consectetur adipiscing elit, sed do eiusmod tempor incididunt ut labore et dolore magna aliqua. Ut enim ad minim veniam.</p>
      <p><strong>Haltbarkeit:</strong> Nach dem Öffnen 6 Monate haltbar</p>
    </div>

    <div class="divider"></div>

    <div class="inside-col inside-col--warnings">
      <p><strong>ACHTUNG:</strong> Kann Schläfrigkeit und Benom­menheit verursachen Enthält D-Limonen, Citral. Kann allergische Reaktionen hervor­rufen. Darf nicht in die Hände von Kindern gelangen.</p>
      <p><strong>ATTENTION:</strong> Peut provoquer somnolence ou vertiges. Contient d-limonène, citral. Peut produire une réaction allergique. Tenir hors de portée des enfants.</p>
    </div>
  </section>

</body>
</html>
```